Business Card Design

We are a commercial real estate brokerage in San Francisco, leasing office buildings downtown.
I would like a clean, elegant look. Simple but powerful .

Industry/Entity Type

Business

Contact Information for Business Card

Derek Holloway
lic# 07258143
415.555.0172
derek@velt-commercial.example
velt-commercial.example

```html
<!DOCTYPE html>
<html lang="en">
<head>
<meta charset="utf-8">
<title>Velt Commercial – Business Card</title>
<link rel="stylesheet" href="https://fonts.googleapis.com/css2?family=Source+Sans+3:ital,wght@0,400;0,600;1,400&display=swap">
<style>
  :root {
    --backdrop: #8e8e8e;
    --card: #eaebed;
    --card-back: #e8e9eb;
    --skyline-light: #e2e3e6;
    --skyline-dark: #d3d5d9;
    --slate: #5e7290;
    --ink: #56585c;
    --ink-soft: #5a5c60;
  }
  * { margin: 0; padding: 0; box-sizing: border-box; }
  html, body { width: 1105px; height: 1200px; overflow: hidden; }
  body {
    background: var(--backdrop);
    font-family: "Source Sans 3", "Myriad Pro", Arial, sans-serif;
    position: relative;
  }
  .card {
    position: absolute;
    left: 182px;
    width: 746px;
    height: 424px;
    overflow: hidden;
  }
  .card--front { top: 120px; background: var(--card); }
  .card--back { top: 636px; background: var(--card-back); }

  .skyline-art {
    position: absolute;
    inset: 0;
    background: linear-gradient(180deg, var(--skyline-light) 0%, var(--skyline-dark) 100%);
    opacity: .75;
  }
  .contact-block {
    position: absolute;
    left: 114px;
    top: 96px;
    color: var(--ink);
  }
  .contact-name {
    font-size: 26px;
    font-weight: 600;
    color: var(--slate);
    letter-spacing: .3px;
    text-transform: uppercase;
  }
  .contact-license { font-size: 19px; margin-top: 10px; }
  .contact-list { list-style: none; margin-top: 16px; }
  .contact-list li {
    display: flex;
    align-items: center;
    gap: 11px;
    font-size: 19px;
    line-height: 28px;
  }
  .contact-list svg { width: 16px; height: 16px; fill: var(--slate); flex: none; }
  .tagline {
    margin-top: 24px;
    font-size: 18.5px;
    font-style: italic;
    line-height: 28px;
    color: var(--ink-soft);
  }

  .brand {
    position: absolute;
    left: 0; right: 0;
    top: 160px;
    display: flex;
    justify-content: center;
    align-items: center;
    gap: 20px;
  }
  .brand-mark { width: 22px; height: 22px; background: var(--slate); }
  .brand-name {
    font-size: 62px;
    font-weight: 600;
    color: var(--slate);
    letter-spacing: 1px;
    text-transform: uppercase;
    line-height: 1;
  }
  .card-stripe {
    position: absolute;
    left: 0; right: 0;
    bottom: 0;
    height: 11px;
    background: var(--slate);
  }
</style>
</head>
<body>
  <section class="card card--front">
    <div class="skyline-art" role="img" aria-label="Faint illustration of a downtown city skyline with office towers"></div>
    <div class="contact-block">
      <h1 class="contact-name">Derek Holloway</h1>
      <p class="contact-license">lic# 07258143</p>
      <ul class="contact-list">
        <li>
          <svg viewBox="0 0 16 16" aria-hidden="true"><path d="M3.6 1.2l2.3 2.6-1.2 1.9c.9 2 2.6 3.7 4.6 4.6l1.9-1.2 2.6 2.3-1.4 2.6C6.9 13.9 2.1 9.1 1 3.6z"/></svg>
          415.555.0172
        </li>
        <li>
          <svg viewBox="0 0 16 16" aria-hidden="true"><path d="M1 3.5h14v9H1zM1.8 4.3L8 9l6.2-4.7z" fill-rule="evenodd"/></svg>
          derek@velt-commercial.example
        </li>
        <li>
          <svg viewBox="0 0 16 16" aria-hidden="true"><circle cx="8" cy="8" r="7"/><path d="M4 5.5h3v3H5zM9 9h3l-1 3H9z" fill="#eaebed"/></svg>
          velt-commercial.example
        </li>
      </ul>
      <p class="tagline">commercial real estate brokerage in San Francisco<br>leasing office buildings downtown.</p>
    </div>
  </section>

  <section class="card card--back">
    <div class="brand">
      <span class="brand-mark" aria-hidden="true"></span>
      <span class="brand-name">Velt Commercial</span>
    </div>
    <div class="card-stripe"></div>
  </section>
</body>
</html>
```